Business Card Design

Business Card for professional consulting firm working with large financial institutions.

Target Market(s)

Executive buyers

Industry/Entity Type

Banking

Contact Information for Business Card

Mild creativity wanted. Not boring, but do elaborate artwork.

Font styles to use
Serif
Sans Serif

Colors

Designer to choose colors to be used in the design.

Requirements
Must have
• Standard business card features - company name, individual name, telephone, website, email, locations.
Nice to have
• Two colors
Should not have
• too many colors, fancy printing, cartoons.

```html
<!DOCTYPE html>
<html lang="en">
<head>
<meta charset="utf-8">
<title>k7advisory — Business Card</title>
<link rel="stylesheet" href="https://fonts.googleapis.com/css2?family=Roboto:wght@400;500&family=Roboto+Condensed:wght@700&display=swap">
<style>
  :root {
    --backdrop: #e9e6e1;
    --card-front: #f3f3f3;
    --card-back: #c4c4c4;
    --ink: #111111;
    --ink-soft: #4a4a4a;
    --ink-muted: #b3b3b3;
    --accent-grey: #9a9a9a;
    --white: #ffffff;
    --rule: #333333;
  }
  * { margin: 0; padding: 0; box-sizing: border-box; }
  html, body {
    width: 1200px; height: 960px; overflow: hidden;
    background: var(--backdrop);
    font-family: "Roboto", Arial, sans-serif;
  }
  .canvas { position: relative; width: 1200px; height: 960px; }

  .card { position: absolute; width: 601px; height: 343px; box-shadow: 0 3px 6px rgba(0,0,0,.25); }
  .card--front { left: 314px; top: 113px; background: var(--card-front); }
  .card--back  { left: 312px; top: 472px; width: 600px; background: var(--card-back); }

  .accent-tab { position: absolute; left: 0; top: 51px; width: 8px; height: 46px; }
  .accent-tab__top { height: 23px; background: var(--accent-grey); }
  .accent-tab__bottom { height: 23px; background: var(--ink); }

  .holder { position: absolute; left: 38px; top: 53px; }
  .holder__name {
    font-family: "Roboto Condensed", Arial, sans-serif; font-weight: 700;
    font-size: 23px; color: var(--ink); letter-spacing: .2px; line-height: 1;
  }
  .holder__title { margin-top: 6px; font-size: 14px; font-weight: 500; color: var(--ink-muted); line-height: 1; }

  .rule { position: absolute; left: 36px; width: 168px; border-top: 2px dotted var(--rule); }
  .rule--top { top: 115px; }
  .rule--bottom { top: 204px; }

  .address { position: absolute; left: 38px; top: 137px; font-size: 14px; line-height: 18px; color: var(--ink-soft); }

  .contacts { position: absolute; left: 38px; top: 228px; list-style: none; font-size: 14px; line-height: 19.5px; color: var(--ink-soft); }
  .contacts li { display: flex; align-items: center; gap: 7px; }
  .contacts svg { width: 13px; height: 13px; fill: var(--ink); flex: none; }

  .brand { position: absolute; display: flex; align-items: center; gap: 12px; font-family: "Roboto", Arial, sans-serif; font-weight: 400; }
  .brand__dot { width: 14px; height: 14px; border-radius: 50%; }
  .brand--front { left: 315px; top: 146px; font-size: 36px; color: var(--ink); }
  .brand--front .brand__dot { background: var(--ink-muted); }
  .brand--back { left: 0; right: 0; top: 145px; justify-content: center; font-size: 38px; color: var(--white); }
  .brand--back .brand__dot { background: var(--white); }

  .web-line {
    position: absolute; left: 0; right: 0; top: 280px; text-align: center;
    font-size: 14px; letter-spacing: 6.4px; color: var(--white);
  }
</style>
</head>
<body>
<main class="canvas">
  <section class="card card--front" aria-label="Business card front">
    <div class="accent-tab"><div class="accent-tab__top"></div><div class="accent-tab__bottom"></div></div>
    <div class="holder">
      <h1 class="holder__name">DANIEL HART</h1>
      <p class="holder__title">CEO/FOUNDER</p>
    </div>
    <div class="rule rule--top"></div>
    <address class="address" style="font-style:normal">k7advisory<br>4120 Larkspur Court<br>Juneau, Alaska 34812</address>
    <div class="rule rule--bottom"></div>
    <ul class="contacts">
      <li><svg viewBox="0 0 24 24" aria-hidden="true"><path d="M6.6 10.8a15.1 15.1 0 0 0 6.6 6.6l2.2-2.2c.3-.3.7-.4 1-.2 1.1.4 2.3.6 3.6.6.6 0 1 .4 1 1V20c0 .6-.4 1-1 1A17 17 0 0 1 3 4c0-.6.4-1 1-1h3.5c.6 0 1 .4 1 1 0 1.3.2 2.5.6 3.6.1.3 0 .7-.2 1z"/></svg>612 550 3914</li>
      <li><svg viewBox="0 0 24 24" aria-hidden="true"><path d="M2 5h20v14H2z M2 5l10 8 10-8" fill="none" stroke="#111" stroke-width="0"/><path d="M2 6l10 7 10-7v13H2z"/><path d="M2 4h20l-10 7z"/></svg>info@k7advisory.com</li>
      <li><svg viewBox="0 0 24 24" aria-hidden="true"><circle cx="12" cy="12" r="10"/><path d="M7 8c2 0 3 1 3 3s2 2 2 4-1 3-1 5M14 4c0 2 1 3 3 3s3 2 3 3" fill="none" stroke="#f3f3f3" stroke-width="2"/></svg>www.k7advisory.com</li>
    </ul>
    <div class="brand brand--front"><span class="brand__dot"></span><span class="brand__name">k7advisory</span></div>
  </section>

  <section class="card card--back" aria-label="Business card back">
    <div class="brand brand--back"><span class="brand__dot"></span><span class="brand__name">k7advisory</span></div>
    <p class="web-line">www.k7advisory.com</p>
  </section>
</main>
</body>
</html>
```